Dental Practice Billboard Design

We are a newer dental practice in need of a simple but appealing billboard for our growing dental practice to attract new patients. The practice is owned by husband and wife dentists and is family friendly in a small town in Kentucky. We try to be very friendly and caring to our patients. Would prefer a blue background for the billboard and our tooth logo to be prominent. We are partial to the Patua One font used in the image below but please feel free to tweak it as you deem necessary. The shape of the uppercase D and lowercase g are why we like that font, so fonts with a similarly shaped “D” and “g” would work as well. Please include our phone number (555) 847-1390. Please see our website Harlowbrookdentistry.example for more info on the practice if needed. Thank you! Looking forward to seeing your creation.
Updates

The dimensions will be 12ft x 24ft (3.6576m x 7.3152m). Apologies for not including this in the original prompt. Thank you all for your submissions.

Industry/Entity Type

Dental

Font styles to use
Other font styles liked:
• Patua One

Colors
0054AA
0677BA
7BADD7
CADEEF
E8F1F8
0094D4
00A9DD
6FCCEA
C7EBF8
E9F6FB
00AB8E
00BBA5
67D7C9
C6EFE9
E9F9F6
59FF00
82FF00
B8FF75
E3FFCB
F4FFEA

Requirements
Must have
• Phone number, website, Logo, Practice name “Harlow Brook Dentistry”
Should not have
• A tagline or slogan

```html
<!DOCTYPE html>
<html lang="en">
<head>
<meta charset="utf-8">
<title>Harlow Brook Dentistry – Billboard</title>
<link href="https://fonts.googleapis.com/css2?family=Patua+One&display=swap" rel="stylesheet">
<style>
  :root {
    --navy: #012a5c;
    --green: #1eae1e;
    --white: #ffffff;
    --page: #ffffff;
  }
  * { box-sizing: border-box; margin: 0; padding: 0; }
  html, body {
    width: 1071px;
    height: 1200px;
    overflow: hidden;
    background: var(--page);
  }
  .billboard {
    position: absolute;
    left: 40px;
    top: 363px;
    width: 994px;
    height: 473px;
    background: var(--navy);
    box-shadow: 0 4px 14px rgba(0, 0, 0, 0.25);
    font-family: "Patua One", Georgia, serif;
    color: var(--white);
  }
  .brand-mark {
    position: absolute;
    left: 78px;
    top: 80px;
    width: 230px;
    height: 230px;
    border-radius: 50%;
    background: var(--green);
  }
  .practice-name {
    position: absolute;
    left: 372px;
    top: 88px;
    line-height: 1;
  }
  .practice-name .name-main {
    display: block;
    font-size: 86px;
    letter-spacing: 0.5px;
  }
  .practice-name .name-sub {
    display: block;
    margin-top: 18px;
    font-size: 70px;
  }
  .contact {
    position: absolute;
    top: 390px;
    display: flex;
    align-items: center;
    font-size: 33px;
    line-height: 1;
  }
  .contact svg { flex: none; margin-right: 18px; }
  .contact-web { left: 43px; }
  .contact-phone { left: 622px; }
</style>
</head>
<body>
  <main class="billboard">
    <div class="brand-mark" aria-hidden="true"></div>

    <h1 class="practice-name">
      <span class="name-main">Harlow Brook</span>
      <span class="name-sub">Dentistry</span>
    </h1>

    <p class="contact contact-web">
      <svg width="46" height="46" viewBox="0 0 46 46" aria-hidden="true">
        <circle cx="23" cy="23" r="20" fill="none" stroke="var(--green)" stroke-width="4"/>
        <ellipse cx="23" cy="23" rx="9" ry="20" fill="none" stroke="var(--green)" stroke-width="3"/>
        <line x1="3" y1="23" x2="43" y2="23" stroke="var(--green)" stroke-width="3"/>
      </svg>
      Harlowbrookdentistry.example
    </p>

    <p class="contact contact-phone">
      <svg width="46" height="46" viewBox="0 0 46 46" aria-hidden="true">
        <path d="M9 4 L16 4 L19 13 L14 17 Q18 27 28 32 L32 27 L41 30 L41 37 Q40 42 34 42 Q8 38 4 11 Q4 5 9 4 Z" fill="var(--green)"/>
        <path d="M26 10 Q34 12 36 20" fill="none" stroke="var(--green)" stroke-width="3" stroke-linecap="round"/>
        <path d="M27 3 Q41 6 43 19" fill="none" stroke="var(--green)" stroke-width="3" stroke-linecap="round"/>
      </svg>
      (555) 847-1390
    </p>
  </main>
</body>
</html>
```